I want ideas sample designs for my book cover

Hello,

We need a book cover designed in flat and 3D Versions. We would like to have jpg and png for final output and include a copy of the PSD for future revisions.

Here are the basic details:

Title: The Harvest of Quiet Builders
Author: Norman Quillfeather

Dimensions of book:

Was looking at the Pavo website for dimensions. I thought you may want to go on there and look at the different sizes. I used the 6x9” perfect bound US trade size for my book. You will see that this has a spine width of 0.225”, Cover size of 12.48 x 9.25” and spine begins at 6.125”

If you need background info on the author just to get an idea what he does, please check:

http://NormanQuillfeather.example

IMPORTANT: Please see attached document for a more detailed info:

Exact Title Of book
Back Cover
Spine Info
Measurements of book and dimension
Examples of book covers
Norman's photo attached

Thanks,
Darlene

Industry/Entity Type

Life Coaching

Font styles to use
Serif

Requirements
Must have
• Jpg, png and PSD files
• title
• author
• exact dimensions
• front and back cover
• flat and 3d versions

```html
<!DOCTYPE html>
<html lang="en">
<head>
<meta charset="utf-8">
<title>The Harvest of Quiet Builders – Book Cover</title>
<link rel="stylesheet" href="https://fonts.googleapis.com/css2?family=Source+Sans+3:ital,wght@0,400;0,600;1,400&family=Roboto+Condensed:wght@400;700&family=Arimo:wght@700&display=swap">
<style>
  :root {
    --orange: #f26f21;
    --ink: #161311;
    --navy-ink: #1b2233;
    --white: #ffffff;
    --spine-ink: #2a1a10;
    --sky-light: #c9d3dc;
    --sky-mid: #8c9db0;
    --figure-dark: #1a2130;
    --portrait-light: #d8d8d8;
    --portrait-dark: #4a4a4a;
  }
  * { margin: 0; padding: 0; box-sizing: border-box; }
  html, body { width: 1200px; height: 893px; overflow: hidden; background: #fff; }
  .cover { position: relative; width: 1200px; height: 893px; overflow: hidden; }

  /* Back cover */
  .back-cover {
    position: absolute; left: 0; top: 0; width: 618px; height: 893px;
    background: var(--orange);
  }
  .blurb {
    position: absolute; left: 51px; top: 60px; width: 507px;
    font-family: "Source Sans 3", sans-serif; font-size: 13.7px; line-height: 17px;
    color: var(--ink); text-align: justify; hyphens: auto;
  }
  .blurb p + p { margin-top: 17px; }
  .author-portrait {
    position: absolute; left: 48px; top: 624px; width: 155px; height: 155px;
    background: radial-gradient(circle at 55% 45%, var(--portrait-dark) 0 30%, var(--portrait-light) 60%, #f2f2f2 100%);
  }
  .author-bio {
    position: absolute; left: 228px; top: 630px; width: 330px;
    font-family: "Source Sans 3", sans-serif; font-weight: 400; font-size: 10.6px; line-height: 13.7px;
    color: var(--white); text-align: justify; hyphens: auto;
  }
  .website {
    position: absolute; left: 73px; top: 811px;
    font-family: "Source Sans 3", sans-serif; font-style: italic; font-size: 11.2px;
    color: var(--white);
  }
  .isbn-box {
    position: absolute; left: 336px; top: 790px; width: 146px; height: 69px;
    background: var(--white);
    font-family: "Source Sans 3", sans-serif; font-size: 7px; color: var(--ink);
    text-align: center; padding-top: 7px;
  }

  /* Spine */
  .spine-text {
    position: absolute; left: 0; top: 0; width: 618px; height: 893px; pointer-events: none;
  }

  /* Front cover */
  .front-cover {
    position: absolute; left: 618px; top: 0; width: 582px; height: 893px;
  }
  .front-photo {
    position: absolute; inset: 0;
    background:
      radial-gradient(ellipse 48% 70% at 30% 48%, var(--figure-dark) 0 55%, rgba(26,33,48,0) 80%),
      linear-gradient(180deg, var(--sky-light) 0%, #e6ebef 30%, var(--sky-mid) 70%, #3c5168 100%);
  }
  .front-title { position: absolute; inset: 0; }
  .tagline {
    position: absolute; right: 34px; top: 266px; text-align: right;
    font-family: "Source Sans 3", sans-serif; font-size: 20px; line-height: 29.7px;
    color: var(--navy-ink);
  }
  .from-line {
    position: absolute; right: 35px; top: 771px;
    font-family: "Roboto Condensed", sans-serif; font-size: 18.5px; color: var(--white);
    text-shadow: 1px 1px 2px rgba(0,0,0,.6);
  }
</style>
</head>
<body>
<div class="cover">

  <section class="back-cover">
    <div class="blurb">
      <p>This path goes way beyond Entrepreneurism! This is a book for the awakening Entrepreneurs who are building businesses for a better world, affecting generations to come. Bringing you disruptive (in a good way) information, to turn you and your business inside-out for maximum acceleration towards your organisational vision, mission and values.</p>
      <p>There is the potential to have a more meaningful life and business by discovering the symbiotic relationship that exists between all beings. You will be empowered to take your life and business to the next level if you answer the call in this book. It will introduce you to the power of Amazonian plant medicine and other entheogens for improving relationships with yourself, your partner and your family, friends, business associates and Mother Earth.</p>
      <p>An entheogen is defined as ‘a substance (usually from a plant, but not always) that is consumed in order to alter one’s state of consciousness or to act as a catalyst towards encounters with other states of being.’ Plant medicine has been successfully used in South America for thousands of years. This ancient wisdom is helping billionaires, industry icons and entrepreneurs to be better leaders, awakening to its potential for allowing deep examination of the psyche which has the ability to heal, eliminate fears and create a new level of success both personally and professionally.</p>
      <p>Norman shares his own heart-felt personal experiences and insights gained from working with these substances and the amazing medicine men and women of the Amazon who retain thousands of years of ancient wisdom. He has spent years turning himself inside-out to powerfully transform his own life and business and wants to encourage entrepreneurs to do the same. He believes that if enough people have the opportunity to explore their own consciousness, then together we can make a positive impact on humanity. If you are ready to travel to the fringes and take a journey within, you will discover that you are the missing link you have been looking for. Get ready to expand your consciousness, transform your business and create a new inspiring lifestyle, which will benefit all beings and our beautiful Mother Earth.</p>
    </div>

    <div class="author-portrait" role="img" aria-label="Black and white portrait photo of the author, smiling"></div>

    <p class="author-bio">Norman Quillfeather is an internationally-renowned entrepreneur, speaker, philanthropist, thought leader and best-selling author. Having played the role of transformational coach, facilitator and spoken to over three million people from twelve different countries, he challenges you in his second book to journey deep within yourself to examine the core of your true nature and how it impacts your entrepreneurial journey. Some of the world biggest game changers, social entrepreneurs, internet marketers and consultants have reported that Norman’s golden edge is to integrate “purpose with profits” in a way that brings greater meaning to the work they are doing here in the world.</p>

    <p class="website">www.NormanQuillfeather.example</p>

    <div class="isbn-box">ISBN</div>
  </section>

  <svg class="spine-text" width="618" height="893" viewBox="0 0 618 893" aria-label="Spine">
    <text transform="translate(601,70) rotate(90)" textLength="285" lengthAdjust="spacingAndGlyphs"
          font-family="'Source Sans 3', sans-serif" font-weight="600" font-size="13" fill="var(--spine-ink)" letter-spacing="1">The HARVEST OF QUIET BUILDERS</text>
    <text transform="translate(601,708) rotate(90)" textLength="96" lengthAdjust="spacingAndGlyphs"
          font-family="'Source Sans 3', sans-serif" font-size="13" fill="var(--white)">Norman Quillfeather</text>
  </svg>

  <section class="front-cover">
    <div class="front-photo" role="img" aria-label="Photo of a man seen from behind over his shoulder, gazing out at the sea under a pale sky"></div>

    <svg class="front-title" width="582" height="893" viewBox="0 0 582 893">
      <defs>
        <filter id="title-shadow" x="-10%" y="-10%" width="130%" height="130%">
          <feDropShadow dx="3" dy="3" stdDeviation="2" flood-color="#000" flood-opacity=".55"/>
        </filter>
      </defs>
      <g font-family="Arimo, sans-serif" font-weight="700" fill="var(--orange)" filter="url(#title-shadow)">
        <text transform="translate(114,768) rotate(-90)" font-size="104" textLength="736" lengthAdjust="spacingAndGlyphs">HARVEST OF</text>
        <text transform="translate(228,852) rotate(-90)" font-size="104" textLength="816" lengthAdjust="spacingAndGlyphs">QUIET BUILDERS</text>
        <text x="38" y="850" font-size="58" textLength="76" lengthAdjust="spacingAndGlyphs">The</text>
      </g>
      <text x="547" y="849" text-anchor="end" font-family="Arimo, sans-serif" font-weight="700" font-size="40"
            fill="var(--white)" filter="url(#title-shadow)" textLength="287" lengthAdjust="spacingAndGlyphs">Norman Quillfeather</text>
    </svg>

    <p class="tagline">How this<br>ANCIENT<br>WISDOM<br>is helping<br>billionaires,<br>INDUSTRY<br>ICONS and<br>entrepreneurs<br>to be better<br>LEADERS,<br>increase impact<br>and leave a LEGACY</p>

    <p class="from-line">From the Best Selling Author of “Stillwater”</p>
  </section>

</div>
</body>
</html>
```